Property management company looking for modern card design

We at Blue Heron Partners provides property management services for its residential and commercial properties, with expertise in all categories of multifamily, industrial and office projects throughout California.

We need a business card design that is professional and modern designed business card. In our field, clients get hundreds of business cards, we would like our card to stand out.

Please avoid small print.

Target Market(s)

Professionals and high end clients

Industry/Entity Type

Financial Planning

Contact Information for Business Card

Company Name: Blue Heron Partners, Name, email, license #, phone number, website blueheronpartners.com

Font styles to use
Sans Serif

Requirements
Must have
• The card design needs to be adaptable because there is a possibly we will be expanding into different sectors other than real estate. The card design should be focused on financial planning and asset management.
Nice to have
• Modern and simple business card. Eye catching. Non-standard size/shaped cards would be great.
• blueheronpartners.com
Should not have
• Too many bright color or any pictures or shapes of real estate stuff.

```html
<!DOCTYPE html>
<html lang="en">
<head>
<meta charset="UTF-8">
<title>Blue Heron Partners – Business Card</title>
<link href="https://fonts.googleapis.com/css2?family=Montserrat:wght@400;500;700&display=swap" rel="stylesheet">
<style>
  :root {
    --accent: #c8302e;
    --ink: #2b2b2b;
    --card: #ffffff;
    --backdrop: #e9e7e4;
  }
  * { margin: 0; padding: 0; box-sizing: border-box; }
  html, body {
    width: 1200px; height: 1000px; overflow: hidden;
    background: var(--backdrop);
    font-family: "Montserrat", Arial, sans-serif;
    color: var(--ink);
  }
  .stage { position: relative; width: 1200px; height: 1000px; }
  .card {
    position: absolute; left: 288px; width: 625px; height: 357px;
    background: var(--card); border-radius: 26px; overflow: hidden;
    box-shadow: 0 6px 18px rgba(0,0,0,0.18);
  }
  .card--front { top: 140px; }
  .card--back { top: 532px; }

  .wordmark {
    display: flex; align-items: center; gap: 12px;
    font-weight: 400; letter-spacing: 0.5px; color: var(--ink);
    white-space: nowrap;
  }
  .wordmark__dot {
    border-radius: 50%; background: var(--accent); flex: none;
  }
  .card--front .wordmark {
    position: absolute; left: 0; right: 0; top: 155px;
    justify-content: center; font-size: 31px;
  }
  .card--front .wordmark__dot { width: 26px; height: 26px; }
  .card--back .wordmark {
    position: absolute; right: 34px; top: 46px; font-size: 20px; gap: 9px;
  }
  .card--back .wordmark__dot { width: 17px; height: 17px; }

  .holder__bar {
    position: absolute; left: 0; top: 41px; width: 8px; height: 36px;
    background: var(--accent);
  }
  .holder { position: absolute; left: 34px; top: 36px; }
  .holder__name { font-size: 22px; font-weight: 700; color: var(--accent); line-height: 1.15; }
  .holder__title { font-size: 15px; font-weight: 400; line-height: 1.3; }

  .license {
    position: absolute; left: 36px; top: 222px; font-size: 15px;
  }
  .license__label { color: var(--accent); }

  .contacts {
    position: absolute; left: 36px; top: 257px; list-style: none;
    font-size: 15px; line-height: 23px;
  }
  .contacts li { display: flex; align-items: center; gap: 8px; }
  .contacts svg { width: 12px; height: 12px; fill: var(--accent); flex: none; }
</style>
</head>
<body>
<main class="stage">
  <section class="card card--front" aria-label="Card front">
    <div class="wordmark">
      <span class="wordmark__dot"></span>
      <span class="wordmark__text">BLUE HERON PARTNERS</span>
    </div>
  </section>

  <section class="card card--back" aria-label="Card back">
    <span class="holder__bar"></span>
    <div class="holder">
      <p class="holder__name">Daniel Reyes</p>
      <p class="holder__title">President</p>
    </div>

    <div class="wordmark">
      <span class="wordmark__dot"></span>
      <span class="wordmark__text">BLUE HERON PARTNERS</span>
    </div>

    <p class="license"><span class="license__label">License</span>: #7310458</p>

    <ul class="contacts">
      <li>
        <svg viewBox="0 0 24 24"><path d="M6.6 10.8a15.1 15.1 0 0 0 6.6 6.6l2.2-2.2a1 1 0 0 1 1-.25 11.4 11.4 0 0 0 3.6.57 1 1 0 0 1 1 1V20a1 1 0 0 1-1 1A17 17 0 0 1 3 4a1 1 0 0 1 1-1h3.5a1 1 0 0 1 1 1c0 1.25.2 2.45.57 3.57a1 1 0 0 1-.25 1z"/></svg>
        555-0142-7788
      </li>
      <li>
        <svg viewBox="0 0 24 24"><path d="M2 5h20v14H2z M2 5l10 8 10-8" /><path d="M2 6.5V19h20V6.5l-10 8z" fill="#a02523"/></svg>
        info@blueheronpartners.com
      </li>
      <li>
        <svg viewBox="0 0 24 24"><path d="M12 2a10 10 0 1 0 0 20 10 10 0 0 0 0-20zm6.9 6h-2.9a15.6 15.6 0 0 0-1.4-3.6A8 8 0 0 1 18.9 8zM12 4c.8 1.2 1.5 2.5 1.9 4h-3.8c.4-1.5 1.1-2.8 1.9-4zM4.3 14a8 8 0 0 1 0-4h3.4a16.5 16.5 0 0 0 0 4zm.8 2h2.9c.3 1.3.8 2.5 1.4 3.6A8 8 0 0 1 5.1 16zM8 8H5.1a8 8 0 0 1 4.3-3.6C8.8 5.5 8.3 6.7 8 8zm4 12c-.8-1.2-1.5-2.5-1.9-4h3.8c-.4 1.5-1.1 2.8-1.9 4zm2.3-6H9.7a14.7 14.7 0 0 1 0-4h4.6a14.7 14.7 0 0 1 0 4zm.3 5.6c.6-1.1 1.1-2.3 1.4-3.6h2.9a8 8 0 0 1-4.3 3.6zm1.7-5.6a16.5 16.5 0 0 0 0-4h3.4a8 8 0 0 1 0 4z"/></svg>
        www.blueheronpartners.com
      </li>
    </ul>
  </section>
</main>
</body>
</html>
```